SkyvornQ Business Cards and Stationary Design

Need a design for our business cards and stationary. I want to carry on the theme of the logo. I want the business cards to have a design on the back. I would like the business cards and the stationary to carry the same theme, design scheme, and branding

Target Market(s)

Airlines and Maintenance Facilities

Industry/Entity Type

Aviation

Contact Information for Business Card

Name
Position Title
Address: 4827 Trellis Hollow Road, Harlow Point, Calvaria, 34951
Office Number
Mobile Number
Email
Website

Font styles to use
Serif
Sans Serif

Colors

Designer to choose colors to be used in the design.

```html
<!DOCTYPE html>
<html lang="en">
<head>
<meta charset="utf-8">
<title>SkyvornQ Business Card</title>
<link href="https://fonts.googleapis.com/css2?family=Roboto:wght@400;500;700&display=swap" rel="stylesheet">
<style>
  :root {
    --navy: #0c2f66;
    --navy-deep: #0a2352;
    --sky: #1ea3e3;
    --sky-soft: #36b2ec;
    --paper: #f7f7f7;
    --ink-light: #ffffff;
    --ink-muted: #3a3a3a;
    --stage: #e9e6e2;
  }
  * { margin: 0; padding: 0; box-sizing: border-box; }
  html, body { width: 1200px; height: 886px; overflow: hidden; }
  body {
    background: var(--stage);
    font-family: "Roboto", Arial, sans-serif;
    position: relative;
  }
  .card {
    position: absolute;
    width: 520px;
    height: 297px;
    border-radius: 16px;
    overflow: hidden;
    background: var(--paper);
    box-shadow: 0 6px 18px rgba(0,0,0,.18);
  }
  .card-back { left: 70px; top: 130px; }
  .card-front { left: 610px; top: 460px; }
  .card svg.shapes { position: absolute; inset: 0; }

  /* back */
  .back-brand {
    position: absolute; left: 34px; bottom: 42px;
    color: var(--navy);
  }
  .back-brand .wordmark {
    font-weight: 700; font-size: 26px; letter-spacing: 5px;
  }
  .back-brand .site {
    font-size: 11px; letter-spacing: 5.5px; color: var(--ink-muted); margin-top: 2px;
  }

  /* front */
  .contact {
    position: absolute; left: 42px; top: 26px;
    color: var(--ink-light); font-size: 13px; line-height: 17px;
  }
  .contact .address { margin-bottom: 4px; padding-left: 20px; }
  .contact li { list-style: none; display: flex; align-items: center; gap: 8px; }
  .contact svg { width: 12px; height: 12px; flex: none; }
  .person {
    position: absolute; left: 30px; top: 192px; color: var(--ink-light);
  }
  .person .name { font-weight: 700; font-size: 21px; letter-spacing: .5px; }
  .person .role { font-size: 14px; }
  .front-brand {
    position: absolute; right: 32px; top: 200px;
    display: flex; align-items: center; gap: 10px;
  }
  .front-brand .mark {
    width: 26px; height: 26px; border-radius: 50%; background: var(--sky);
  }
  .front-brand .wordmark {
    font-weight: 700; font-size: 26px; letter-spacing: 4px; color: var(--navy);
  }
</style>
</head>
<body>

<section class="card card-back" aria-label="Card back">
  <svg class="shapes" viewBox="0 0 520 297" aria-hidden="true">
    <defs>
      <linearGradient id="cornerFill" x1="0" y1="0" x2="1" y2="1">
        <stop offset="0" stop-color="#1a5fb0"/>
        <stop offset="1" stop-color="#0a2352"/>
      </linearGradient>
    </defs>
    <path d="M335,0 H520 V215 C470,200 448,150 440,110 C430,60 390,20 335,0 Z" fill="url(#cornerFill)"/>
    <circle cx="355" cy="125" r="95" fill="none" stroke="var(--sky)" stroke-width="14"/>
  </svg>
  <div class="back-brand">
    <div class="wordmark">SKYVORNQ</div>
    <div class="site">www.skyvornq.com</div>
  </div>
</section>

<section class="card card-front" aria-label="Card front">
  <svg class="shapes" viewBox="0 0 520 297" aria-hidden="true">
    <defs>
      <linearGradient id="navyFill" x1="0" y1="0" x2="1" y2="1">
        <stop offset="0" stop-color="#123d7d"/>
        <stop offset="1" stop-color="#0a2352"/>
      </linearGradient>
      <linearGradient id="skyFill" x1="0" y1="0" x2="1" y2="1">
        <stop offset="0" stop-color="#36b2ec"/>
        <stop offset="1" stop-color="#1791d6"/>
      </linearGradient>
    </defs>
    <path d="M0,0 H445 C380,40 340,150 240,160 H0 Z" fill="url(#navyFill)"/>
    <path d="M0,164 H190 C250,164 262,250 300,297 H0 Z" fill="url(#skyFill)"/>
  </svg>

  <div class="contact">
    <div class="address">4827 Trellis Hollow Road<br>Harlow Point, Calvaria, 34951</div>
    <ul>
      <li><svg viewBox="0 0 12 12"><path d="M2.5 1 L4.5 1 L5.2 3.5 L4 4.6 C4.6 6 6 7.4 7.4 8 L8.5 6.8 L11 7.5 V9.5 C11 10.3 10.3 11 9.5 11 C5 11 1 7 1 2.5 C1 1.7 1.7 1 2.5 1 Z" fill="#fff"/></svg>555 214 7730</li>
      <li><svg viewBox="0 0 12 12"><rect x="3" y="0.5" width="6" height="11" rx="1.2" fill="none" stroke="#fff" stroke-width="1.2"/></svg>555 390 6152</li>
      <li><svg viewBox="0 0 12 12"><rect x="0.5" y="2.5" width="11" height="7" fill="none" stroke="#fff" stroke-width="1.1"/><path d="M0.5 2.5 L6 6.5 L11.5 2.5" fill="none" stroke="#fff" stroke-width="1.1"/></svg>info@skyvornq.com</li>
      <li><svg viewBox="0 0 12 12"><circle cx="6" cy="6" r="5.5" fill="#fff"/></svg>www.skyvornq.com</li>
    </ul>
  </div>

  <div class="person">
    <div class="name">DARA LINWELL</div>
    <div class="role">CEO/FOUNDER</div>
  </div>

  <div class="front-brand">
    <span class="mark" aria-hidden="true"></span>
    <span class="wordmark">SKYVORNQ</span>
  </div>
</section>

</body>
</html>
```